Business Card Design - Service Company

Use of the card mainly in living rooms and relations b2b We wish a card with a modern design, blue tones in the background would be a plus The card must be front / back (one side with the logo / the other with the information of contact )

Font styles to use
Serif

Requirements
Must have
• Using the map on the back of the business card Editable format! Photoshop CS2 / Illustrator CS2
Nice to have
• Mivrel Data IT Plein Ouest Commercial Center, 20417 Valmorre 0491847352 Siret 41873306200018 APE 9511Z https://www.fb.com/boutiquetech.mivreldata www.mivrel-data.com

```html
<!DOCTYPE html>
<html lang="fr">
<head>
<meta charset="utf-8">
<title>Mivrel Data IT – Business Card</title>
<link href="https://fonts.googleapis.com/css2?family=Roboto:wght@400;500;700&display=swap" rel="stylesheet">
<style>
  :root {
    --page-bg: #e9e9e9;
    --card-white: #ffffff;
    --brand-blue: #2a8bcb;
    --accent-blue: #2b8fd4;
    --text-dark: #111111;
    --text-grey: #555555;
    --divider: #c9c9c9;
    --map-dark: #1f6fa6;
  }
  * { box-sizing: border-box; margin: 0; padding: 0; }
  html, body { width: 1125px; height: 1200px; overflow: hidden; }
  body {
    background: var(--page-bg);
    font-family: "Roboto", Arial, sans-serif;
    position: relative;
  }
  .card {
    position: absolute;
    left: 156px;
    width: 826px;
    height: 472px;
    overflow: hidden;
  }
  .card--front { top: 106px; background: var(--card-white); }
  .card--back { top: 639px; background: var(--brand-blue); }

  /* Front */
  .brand-mark {
    position: absolute;
    left: 30px; top: 220px;
    width: 380px;
    display: flex; align-items: center; justify-content: center; gap: 14px;
  }
  .brand-mark__square { width: 22px; height: 22px; background: var(--accent-blue); }
  .brand-mark__name {
    font-weight: 700; font-size: 38px; color: var(--accent-blue); letter-spacing: 0.5px;
    white-space: nowrap;
  }
  .divider {
    position: absolute; left: 440px; top: 69px;
    width: 2px; height: 331px; background: var(--divider);
  }
  .contact { position: absolute; left: 477px; top: 88px; }
  .contact__name { font-weight: 700; font-size: 31px; color: var(--accent-blue); line-height: 1.1; letter-spacing: 0.5px; }
  .contact__role { font-weight: 500; font-size: 20px; color: var(--text-dark); margin-bottom: 16px; }
  .contact__company { font-weight: 500; font-size: 19px; color: var(--text-grey); line-height: 25px; }
  .contact__line { font-size: 19px; color: var(--text-grey); line-height: 25px; }
  .contact__ids { margin-top: 5px; }
  .contact__links { margin-top: 6px; list-style: none; }
  .contact__links li { display: flex; align-items: center; gap: 12px; font-size: 19px; color: var(--text-grey); line-height: 26px; }
  .icon { width: 17px; height: 17px; flex: none; }

  /* Back */
  .back-mark {
    position: absolute; left: 0; top: 200px; width: 649px;
    display: flex; align-items: center; justify-content: center; gap: 16px;
  }
  .back-mark__square { width: 30px; height: 30px; background: var(--card-white); }
  .back-mark__name { font-weight: 700; font-size: 48px; color: var(--card-white); white-space: nowrap; }
  .back-url {
    position: absolute; left: 0; width: 649px; top: 394px; text-align: center;
    color: var(--card-white); font-size: 19px; letter-spacing: 4px;
  }
  .location-map {
    position: absolute; right: 0; top: 0; width: 177px; height: 100%;
    background: linear-gradient(180deg, var(--brand-blue), var(--map-dark) 50%, var(--brand-blue));
  }
</style>
</head>
<body>
  <section class="card card--front" aria-label="Card front">
    <div class="brand-mark">
      <span class="brand-mark__square"></span>
      <span class="brand-mark__name">MIVREL DATA IT</span>
    </div>
    <div class="divider"></div>
    <div class="contact">
      <h1 class="contact__name">MARC DELVAUX</h1>
      <p class="contact__role">CEO/FOUNDER</p>
      <p class="contact__company">Mivrel Data IT</p>
      <p class="contact__line">Plein Ouest Commercial Center</p>
      <p class="contact__line">20417 Valmorre</p>
      <div class="contact__ids">
        <p class="contact__line">Siret 41873306200018</p>
        <p class="contact__line">APE 9511Z</p>
      </div>
      <ul class="contact__links">
        <li>
          <svg class="icon" viewBox="0 0 24 24" aria-hidden="true"><path fill="#2b8fd4" d="M6.6 10.8a15.1 15.1 0 0 0 6.6 6.6l2.2-2.2c.3-.3.7-.4 1-.2 1.1.4 2.3.6 3.6.6.6 0 1 .4 1 1V20c0 .6-.4 1-1 1A17 17 0 0 1 3 4c0-.6.4-1 1-1h3.5c.6 0 1 .4 1 1 0 1.3.2 2.5.6 3.6.1.3 0 .7-.2 1z"/></svg>
          0491847352
        </li>
        <li>
          <svg class="icon" viewBox="0 0 24 24" aria-hidden="true"><rect x="2" y="2" width="20" height="20" rx="3" fill="#2b8fd4"/></svg>
          @mivreldata
        </li>
        <li>
          <svg class="icon" viewBox="0 0 24 24" aria-hidden="true"><circle cx="12" cy="12" r="10" fill="#2b8fd4"/><path d="M2 12h20M12 2c3 3 3 17 0 20M12 2c-3 3-3 17 0 20" stroke="#fff" stroke-width="1.5" fill="none"/></svg>
          www.mivrel-data.com
        </li>
      </ul>
    </div>
  </section>

  <section class="card card--back" aria-label="Card back">
    <div class="back-mark">
      <span class="back-mark__square"></span>
      <span class="back-mark__name">MIVREL DATA IT</span>
    </div>
    <p class="back-url">www.mivrel-data.com</p>
    <div class="location-map" role="img" aria-label="Access map showing the road between two roundabouts and the shop location"></div>
  </section>
</body>
</html>
```